New Wix logo and website layout

I need a new logo design and a new, modern website layout design. I am a professional therapist providing remedial massage. I am Canadian but live in Australia & would like the logo to have a somewhat 'Canadian feel' to it (something subtle i.e. no flags) I currently have a maple tree leaf as my logo. my current website is tidewaterbodywork.com.au. I need the website to work on mobile phones & traditional web browsers.

Target Market(s)

customers looking for remedial massage and manual lymphatic drainage

Industry/Entity Type

professional massage

Coding

Coded - Design and coding required

Font styles to use
Sans Serif

Colors
EB3D1F
EC4F4E
F09395
F8D3D4
FCEDEE

Requirements
Nice to have
• something subtle that indicates that I am canadian
Should not have
• no flags. nothing too bold

```html
<!DOCTYPE html>
<html lang="en">
<head>
<meta charset="utf-8">
<title>Tidewater Bodywork – Remedial Massage</title>
<link rel="stylesheet" href="https://fonts.googleapis.com/css2?family=DM+Serif+Display&family=Nunito+Sans:wght@400;600;700;800&display=swap">
<style>
:root{
  --red:#EB3D1F;
  --coral:#EC4F4E;
  --rose:#F09395;
  --blush:#F8D3D4;
  --shell:#FCEDEE;
  --ink:#1d1d1d;
  --grey:#ececec;
  --footer:#1b1b1b;
  --white:#fff;
  --serif:"DM Serif Display", Georgia, serif;
  --sans:"Nunito Sans", Arial, sans-serif;
}
*{box-sizing:border-box;margin:0;padding:0}
html,body{width:1200px;height:3050px;overflow:hidden}
body{position:relative;background:var(--white);font-family:var(--sans);color:var(--ink)}
a{color:inherit;text-decoration:none}

/* Section titles */
.section-title{font-family:var(--serif);font-size:25px;font-weight:400;color:var(--ink);display:inline-block;padding:12px 0}
.section-title::before{content:"";position:absolute;right:0;top:0;width:84px;height:2px;background:var(--red)}
.section-title::after{content:"";position:absolute;left:2px;bottom:0;width:40px;height:2px;background:var(--red)}
.section-title.is-inline{position:relative}

/* Header */
.site-header{left:0;top:0;width:1200px;height:78px;background:var(--white)}
.brand{display:flex;align-items:center;gap:12px;font-family:var(--serif);font-size:20px;color:var(--ink)}
.brand-dot{width:44px;height:44px;border-radius:50%;background:var(--red)}
.header-brand{left:132px;top:17px}
.main-nav{left:432px;top:29px;display:flex;font-size:13px;font-weight:600;letter-spacing:.2px}
.main-nav a{padding:0 15px}
.main-nav a.is-active{color:var(--red);border:1px solid var(--red);padding:3px 9px;margin-top:-4px}
.call-box{left:900px;top:0;width:300px;height:78px;background:var(--red);clip-path:polygon(10px 0,100% 0,100% 100%,20px 100%);color:var(--white)}
.call-box svg{position:absolute;left:22px;top:24px}
.call-label{position:absolute;left:61px;top:22px;font-size:11px;font-weight:700}
.call-number{position:absolute;left:61px;top:36px;font-size:17px;font-weight:800}

/* Hero */
.hero{left:0;top:78px;width:1200px;height:531px;overflow:hidden;
  background:
    radial-gradient(ellipse 260px 200px at 560px 250px,#8a5a3e 0%,rgba(138,90,62,0) 100%),
    radial-gradient(ellipse 300px 260px at 1040px 160px,#f1efec 0%,rgba(241,239,236,0) 100%),
    radial-gradient(ellipse 260px 200px at 120px 120px,#a9c47a 0%,rgba(169,196,122,0) 100%),
    linear-gradient(180deg,#cdb89a 0%,#b08a66 45%,#8a5c3c 75%,#9c6a46 100%)}
.hero-title{position:absolute;left:0;width:1200px;bottom:-34px;text-align:center;font-family:var(--serif);font-weight:400;font-size:168px;line-height:1;color:var(--white);letter-spacing:-2px}
.slider-arrow{position:absolute;top:240px;width:50px;height:50px;border-radius:50%;background:var(--coral)}
.slider-arrow svg{position:absolute;left:17px;top:15px}
.arrow-prev{left:-16px}
.arrow-next{right:-16px}

/* Services */
.services-mark{left:150px;top:715px;width:170px;height:170px;border-radius:50%;background:var(--red)}
.services-title{left:373px;top:772px}
.service-card{border-radius:18px;overflow:hidden}
.service-card .label{position:absolute;left:22px;bottom:18px;font-family:var(--serif);font-size:16px;color:var(--white);padding-top:8px}
.service-card .label::before{content:"";position:absolute;left:0;top:0;width:82px;height:1.5px;background:var(--white)}
.card-remedial{left:568px;top:687px;width:240px;height:257px;background:radial-gradient(ellipse 120px 80px at 110px 110px,#e2b89c,rgba(226,184,156,0)),linear-gradient(180deg,#f2ece6 0%,#b58a74 45%,#6a4c40 80%,#2a2220)}
.card-pregnancy{left:826px;top:687px;width:240px;height:257px;background:radial-gradient(ellipse 90px 110px at 150px 140px,#e0a57a,rgba(224,165,122,0)),linear-gradient(135deg,#5f9a7e 0%,#8fae6c 35%,#e3b54a 65%,#3a2a1c)}
.card-deep{left:131px;top:972px;width:298px;height:257px;background:radial-gradient(ellipse 130px 110px at 150px 150px,#7a4a34,rgba(122,74,52,0)),linear-gradient(180deg,#e4e2de 0%,#9a7060 40%,#4a3026 80%,#2a2220)}
.card-therapeutic{left:450px;top:972px;width:298px;height:257px;background:radial-gradient(ellipse 90px 80px at 200px 130px,#a9a9a9,rgba(169,169,169,0)),linear-gradient(160deg,#8ccac4 0%,#b9a08e 40%,#7f7f7f 70%,#2a2624)}
.card-lymphatic{left:767px;top:972px;width:298px;height:257px;background:radial-gradient(ellipse 120px 90px at 120px 160px,#c48a68,rgba(196,138,104,0)),linear-gradient(160deg,#e6d8cc 0%,#b88a70 45%,#5a3e30 75%,#231c19)}

/* Remedial band */
.remedial-band{left:0;top:1283px;width:1200px;height:419px;background:var(--red)}
.remedial-photo{position:absolute;left:530px;top:0;width:670px;height:419px;
  background:
    linear-gradient(90deg,var(--red) 0%,rgba(235,61,31,.5) 14%,rgba(235,61,31,0) 30%),
    radial-gradient(ellipse 120px 50px at 330px 360px,#b3201a,rgba(179,32,26,0)),
    radial-gradient(ellipse 200px 90px at 360px 250px,#e6b49a,rgba(230,180,154,0)),
    linear-gradient(180deg,#f6ede6 0%,#ecd3c4 45%,#e9e4e0 80%,#d9cfca 100%)}
.remedial-title{left:127px;top:1335px;font-family:var(--serif);font-weight:400;font-size:25px;color:var(--white);padding:12px 0}
.remedial-title::before{content:"";position:absolute;left:110px;top:0;width:84px;height:2px;background:var(--white)}
.remedial-title::after{content:"";position:absolute;left:0;bottom:0;width:96px;height:2px;background:var(--white)}
.remedial-text{left:127px;top:1425px;width:366px;font-size:14.5px;line-height:20px;color:var(--white)}
.btn{display:inline-block;font-family:var(--serif);font-size:14px;border-radius:16px;padding:6px 17px}
.btn-light{left:127px;top:1619px;background:var(--white);color:var(--red)}
.btn-red{left:638px;top:2137px;background:var(--red);color:var(--white)}

/* About */
.about-card{left:130px;top:1757px;width:936px;height:460px;border-radius:24px;background:var(--shell)}
.about-photo{left:171px;top:1802px;width:415px;height:367px;border-radius:18px;background:radial-gradient(ellipse 170px 110px at 200px 180px,#d9a384,rgba(217,163,132,0)),linear-gradient(180deg,#e9e5e1 0%,#c9a08a 40%,#a6735a 70%,#f0eeec 100%)}
.about-title{left:634px;top:1795px}
.about-title::before{right:auto;left:67px;width:28px}
.about-title::after{width:40px}
.about-text{left:634px;top:1883px;width:375px;font-size:14.5px;line-height:21.6px;text-align:justify}
.about-text p+p{margin-top:21.6px}

/* Fees */
.fees-section{left:0;top:2277px;width:1200px;height:568px;background:var(--grey)}
.fees-title{left:0;top:2313px;width:1200px;text-align:center}
.fees-title .section-title::before{width:46px;left:0;right:auto}
.fees-title .section-title::after{width:46px;left:0}
.fee-card{top:2395px;width:226px;height:182px;border-radius:16px;background:var(--white);text-align:center}
.fee-price{display:inline-block;margin-top:44px;padding-top:7px;font-family:var(--serif);font-size:21px;color:var(--red);position:relative}
.fee-price::before{content:"";position:absolute;left:50%;top:0;width:60px;margin-left:-30px;height:2px;background:var(--red)}
.fee-price::after{content:"";position:absolute;left:50%;bottom:-5px;width:60px;margin-left:-30px;height:2px;background:var(--red)}
.fee-length{margin-top:20px;font-family:var(--serif);font-size:16px}
.fee-name{margin-top:6px;font-family:var(--serif);font-size:16px}
.fee-extra{left:432px;top:2615px;width:336px;height:56px;border-radius:14px;background:var(--white);display:flex;align-items:center;justify-content:center;gap:12px;font-family:var(--serif);font-size:16px}
.fee-extra strong{font-weight:400;color:var(--red);font-size:21px}
.leaf-band{left:0;top:2690px;width:1200px;height:155px;background:linear-gradient(180deg,rgba(236,236,236,0) 0%,#e9b070 30%,#e4763c 60%,#d94a24 85%,#c9421f)}

/* Footer */
.site-footer{left:0;top:2845px;width:1200px;height:205px;background:var(--footer);color:var(--white)}
.footer-brand{position:absolute;left:130px;top:43px;color:var(--white)}
.footer-contact{position:absolute;right:136px;top:40px;font-size:13px;color:var(--white)}
.footer-contact .sep{margin:0 12px 0 22px}
.footer-nav{position:absolute;right:134px;top:73px;display:flex;gap:30px;font-size:13px;color:var(--white)}
.footer-rule{position:absolute;left:130px;top:125px;width:936px;height:1px;background:#3a3a3a}
.copyright{position:absolute;left:0;top:162px;width:1200px;text-align:center;font-size:11px;color:var(--white)}

/* positioning utility last so it wins */
.abs{position:absolute}
</style>
</head>
<body>

<header class="site-header abs">
  <a class="brand header-brand abs" href="#"><span class="brand-dot"></span>Tidewater Bodywork</a>
  <nav class="main-nav abs">
    <a class="is-active" href="#">HOME</a>
    <a href="#">REMEDIAL MASSAGE</a>
    <a href="#">ABOUT ME</a>
    <a href="#">FEES</a>
    <a href="#">CONTACT</a>
  </nav>
  <div class="call-box abs">
    <svg width="28" height="28" viewBox="0 0 24 24" fill="#fff"><path d="M6.6 10.8a15.1 15.1 0 0 0 6.6 6.6l2.2-2.2a1 1 0 0 1 1-.25 11.4 11.4 0 0 0 3.6.57 1 1 0 0 1 1 1V20a1 1 0 0 1-1 1A17 17 0 0 1 3 4a1 1 0 0 1 1-1h3.5a1 1 0 0 1 1 1c0 1.25.2 2.45.57 3.57a1 1 0 0 1-.25 1z"/></svg>
    <span class="call-label">CALL US</span>
    <span class="call-number">0400 555 018</span>
  </div>
</header>

<section class="hero abs" role="img" aria-label="Photo of a woman relaxing during a hot stone massage with flowers around her">
  <h1 class="hero-title">Deep Tissue</h1>
  <span class="slider-arrow arrow-prev"><svg width="16" height="20" viewBox="0 0 16 20"><path d="M11 2 4 10l7 8" stroke="#fff" stroke-width="2" fill="none"/></svg></span>
  <span class="slider-arrow arrow-next"><svg width="16" height="20" viewBox="0 0 16 20"><path d="M5 2l7 8-7 8" stroke="#fff" stroke-width="2" fill="none"/></svg></span>
</section>

<div class="services-mark abs" aria-hidden="true"></div>
<h2 class="services-title abs section-title">Our Services</h2>
<div class="service-card card-remedial abs" role="img" aria-label="Photo of hands giving a back massage"><span class="label">Remedial</span></div>
<div class="service-card card-pregnancy abs" role="img" aria-label="Photo of a pregnant woman holding her belly"><span class="label">Pregnancy</span></div>
<div class="service-card card-deep abs" role="img" aria-label="Photo of a therapist working deep into a man's back"><span class="label">Deep Tissue</span></div>
<div class="service-card card-therapeutic abs" role="img" aria-label="Photo of a therapist treating a client's knee"><span class="label">Therapeutic</span></div>
<div class="service-card card-lymphatic abs" role="img" aria-label="Photo of a lymphatic drainage leg massage"><span class="label">Lymphatic Drainage</span></div>

<section class="remedial-band abs">
  <div class="remedial-photo" role="img" aria-label="Photo of a woman receiving a shoulder massage beside rose petals"></div>
</section>
<h2 class="remedial-title abs">Remedial massage</h2>
<p class="remedial-text abs">Remedial massage is used to help relieve tension and stress in the soft tissues of the body including muscles, tendons, ligaments and connective tissue. It helps to alleviate soft tissue discomfort associated with everyday and occupational stress, over-use injuries e.g. tendinitis, and many chronic pain conditions. An increase in circulation and increased joint flexibility are additional benefits.</p>
<a class="btn btn-light abs" href="#">Read More</a>

<section class="about-card abs"></section>
<div class="about-photo abs" role="img" aria-label="Photo of a therapist massaging a man's shoulders"></div>
<h2 class="about-title abs section-title">About Me</h2>
<div class="about-text abs">
  <p>I completed my training in Toronto, Canada in 1999 where I obtained a Diploma of Remedial Massage through the Northern College of Massage &amp; Hydrotherapy.</p>
  <p>Over the years, I have practiced in several different settings including medical centre, chiropractic clinic, spa and currently am a sole trader in my own practice. I have been helping my clients achieve better health through my treatments for several years. I take special interest in women's health.</p>
</div>
<a class="btn btn-red abs" href="#">Read More</a>

<section class="fees-section abs"></section>
<div class="fees-title abs"><h2 class="section-title is-inline">Fees</h2></div>
<div class="fee-card abs" style="left:129px"><span class="fee-price">$70.00</span><p class="fee-length">30 min</p><p class="fee-name">Remedial Massage</p></div>
<div class="fee-card abs" style="left:367px"><span class="fee-price">$90.00</span><p class="fee-length">45 min</p><p class="fee-name">Remedial Massage</p></div>
<div class="fee-card abs" style="left:604px"><span class="fee-price">$110.00</span><p class="fee-length">60 min</p><p class="fee-name">Remedial Massage</p></div>
<div class="fee-card abs" style="left:842px"><span class="fee-price">$160.00</span><p class="fee-length">90 min</p><p class="fee-name">Remedial Massage</p></div>
<div class="fee-extra abs">Manual Lymphatic Drainage <strong>$140.00</strong></div>
<div class="leaf-band abs" role="img" aria-label="Border of autumn leaves in orange, red and gold"></div>

<footer class="site-footer abs">
  <a class="brand footer-brand" href="#"><span class="brand-dot"></span>Tidewater Bodywork</a>
  <p class="footer-contact">Tell : 0400 555 018<span class="sep">|</span>E mail : &nbsp;anna@tidewaterbodywork.com.au</p>
  <nav class="footer-nav">
    <a href="#">HOME</a><a href="#">REMEDIAL MASSAGE</a><a href="#">ABOUT ME</a><a href="#">FEES</a><a href="#">CONTACT</a>
  </nav>
  <div class="footer-rule"></div>
  <p class="copyright">Copyright © 2022 All Rights Reserved</p>
</footer>

</body>
</html>
```